Brochure Design Project

hi
Im looking for a great little design for my brochures. I have a home beauty salon and need a brochure menu. The name of the business is Tokari SoftGlow which is a japanese name. I'm not japanese but want it to have a slight feel of japanese, perhaps some watercolour or a traditional pattern.
Salon menu will have waxing, Facials, massage etc and would like a tri fold brochure
No bright colours please or butterflies. I want it to look and feel relaxing and peaceful. Help with a nice Logo would also be great
thanks for your help
Updates

Project Deadline Extended
Reason: I know a lot of you are busy but by extending the timeframe I can hopefully get all your creative minds flowing

hi

Just thought I'd add that I would like the brochures to be modern and edgy looking
thanks so far

Target Market(s)

People that want to be pampered and look and feel great and have a sort of natural feel ( if that makes sense)

Industry/Entity Type

Beauty Salon

Requirements
Must have
• I would like it to be A4 size and folded as a tri brochure,
Nice to have
• A classy font
Should not have
• Butterflies, swirls, bright colours or purple

```html
<!DOCTYPE html>
<html lang="en">
<head>
<meta charset="utf-8">
<title>Tokari SoftGlow – Tri-fold Menu</title>
<link rel="stylesheet" href="https://fonts.googleapis.com/css2?family=Josefin+Sans:ital,wght@0,300;0,400;1,300&display=swap">
<style>
  :root {
    --page: #ecebe8;
    --sky: #93c0ea;
    --mist: #dfe6f4;
    --blush: #f5cddf;
    --pink: #d9639f;
    --pink-soft: #f2b6cf;
    --blue: #7fb1e0;
    --ink: #4a4a55;
    --white: #ffffff;
    --lilac: #cdb8dc;
  }
  * { box-sizing: border-box; margin: 0; padding: 0; }
  html, body { width: 1200px; height: 937px; overflow: hidden; background: var(--page); }
  body { font-family: "Josefin Sans", "Century Gothic", sans-serif; font-weight: 300; color: var(--ink); }
  h2, h3 { font-weight: 300; }

  .brochure {
    position: absolute; left: 20px; top: 59px; width: 1160px; height: 819px;
    background: linear-gradient(180deg, var(--sky) 0%, var(--mist) 45%, var(--blush) 100%);
    box-shadow: 0 3px 14px rgba(0,0,0,.18); overflow: hidden;
  }
  .panel { position: absolute; top: 0; width: 387px; height: 819px; }
  .panel--inside { left: 0; }
  .panel--back { left: 387px; }
  .panel--front { left: 773px; }
  .abs { position: absolute; }

  /* inside fold */
  .blossom-art { left: 0; top: 0; width: 373px; height: 111px;
    background: linear-gradient(180deg, #f4d3e2 0%, rgba(244,211,226,0) 100%); }
  .heading { color: var(--pink); font-size: 23px; letter-spacing: .5px; line-height: 1; }
  .price-list { list-style: none; font-size: 13px; line-height: 17px; }
  .price-list li { display: flex; align-items: baseline; white-space: nowrap; }
  .price-list .leader { flex: 1; border-bottom: 1px solid #9a9aa6; margin: 0 3px; transform: translateY(-2px); }
  .price-list small { font-size: 6px; margin-left: 3px; }
  .waxing-a { left: 39px; top: 128px; width: 145px; }
  .waxing-b { left: 203px; top: 113px; width: 145px; }
  .eyes { left: 203px; top: 245px; width: 145px; }

  .feet-tag { left: 39px; top: 318px; width: 211px; height: 31px; background: var(--white);
    color: var(--blue); font-size: 22px; padding: 6px 8px 0; letter-spacing: .5px; white-space: nowrap; }
  .treatment { left: 39px; width: 309px; }
  .treatment-row { display: flex; align-items: baseline; font-size: 18px; white-space: nowrap; }
  .treatment-row .leader { flex: 1; border-bottom: 1px solid #9a9aa6; margin: 0 4px; transform: translateY(-3px); }
  .treatment-note { font-size: 14px; line-height: 19px; }
  .treatment-desc { font-size: 14px; line-height: 19px; text-align: justify; }
  .band { left: 0; top: 603px; width: 348px; height: 18px; background: var(--blue); }
  .feet-photo { left: 0; top: 621px; width: 348px; height: 198px;
    background: linear-gradient(160deg, #e9e4e2 0%, #f1d9cf 50%, #f4f1ec 100%); }

  /* wordmark */
  .wordmark { text-align: center; color: var(--pink); font-weight: 300; line-height: 1; }
  .wordmark .name { display: block; }
  .wordmark .sub { display: block; letter-spacing: 3px; }
  .back-mark { left: 0; width: 387px; top: 56px; }
  .back-mark .name { font-size: 70px; }
  .back-mark .sub { font-size: 24px; margin-top: 6px; }
  .front-mark { left: 0; width: 387px; top: 350px; }
  .front-mark .name { font-size: 92px; }
  .front-mark .sub { font-size: 30px; margin-top: 6px; }

  /* back panel */
  .services { left: 69px; top: 195px; width: 248px; height: 494px; border: 8px solid var(--white);
    text-align: center; padding-top: 16px; background: rgba(255,255,255,.12); }
  .services h2 { color: var(--pink); font-size: 24px; letter-spacing: 1px; line-height: 1; margin-bottom: 6px; }
  .services h3 { font-size: 18px; line-height: 20px; margin-top: 9px; }
  .services p { font-style: italic; font-size: 13px; line-height: 16px; margin-top: 7px; }
  .services h3 + p { margin-top: 2px; }
  .call { left: 0; width: 387px; top: 738px; text-align: center; font-size: 17px; }
  .call .phone { display: block; color: var(--pink); font-size: 24px; letter-spacing: 1px; margin-top: 6px; }

  /* front panel */
  .address { left: 0; width: 387px; top: 743px; text-align: center; font-size: 17px; line-height: 22px; }
  .address .dot { color: var(--pink); }
</style>
</head>
<body>
<main class="brochure">

  <section class="panel panel--inside">
    <div class="abs blossom-art" role="img" aria-label="Cherry blossom branch illustration"></div>

    <h2 class="abs heading" style="left:39px;top:106px">WAXING</h2>
    <ul class="abs price-list waxing-a">
      <li>1/2 leg<span class="leader"></span>$25.00</li>
      <li>3/4 leg<span class="leader"></span>$35.00</li>
      <li>Full leg<span class="leader"></span>$45.00</li>
      <li>1/2 arm<span class="leader"></span>$20.00</li>
      <li>Full arm<span class="leader"></span>$30.00</li>
      <li>Underarm<span class="leader"></span>$16.00</li>
      <li>Lip<span class="leader"></span>$10.00</li>
      <li>Chin<span class="leader"></span>$12.00</li>
      <li>Chin and Lip<span class="leader"></span>$18.00</li>
    </ul>
    <ul class="abs price-list waxing-b">
      <li>Cheek<span class="leader"></span>$15.00</li>
      <li>Eyebrow tidy<span class="leader"></span>$15.00</li>
      <li>Standard Bikini<span class="leader"></span>$18.00</li>
      <li>G String<span class="leader"></span>$28.00</li>
      <li>Brazilian<small>(all off)</small><span class="leader"></span>$40.00</li>
      <li>Stomach<span class="leader"></span>$15.00</li>
    </ul>
    <h2 class="abs heading" style="left:203px;top:225px">EYES</h2>
    <ul class="abs price-list eyes">
      <li>Lash tint<span class="leader"></span>$15.00</li>
      <li>Brow tint<span class="leader"></span>$12.00</li>
    </ul>

    <h2 class="abs feet-tag">FOR YOUR FEET</h2>

    <div class="abs treatment" style="top:378px">
      <div class="treatment-row">Tiptoe calm massage<span class="leader"></span>$15.00</div>
      <div class="treatment-note">Pure ease. <i>15 min</i></div>
    </div>
    <div class="abs treatment" style="top:443px">
      <div class="treatment-row">Yume Feet means<span class="leader"></span>$50.00</div>
      <div class="treatment-row">gentle renewal</div>
      <p class="treatment-desc">The ultimate foot therapy concentrates on the feet to reduce stress and tension. Consists of a cleansing soak, invigorating sea salt foot scrub, massage and foot mask, ending with a hot towel. A great stress reliever after a long day.</p>
    </div>

    <div class="abs band"></div>
    <div class="abs feet-photo" role="img" aria-label="Photo of feet resting on white sand with daisies"></div>
  </section>

  <section class="panel panel--back">
    <div class="abs wordmark back-mark">
      <span class="name">Tokari</span>
      <span class="sub">SOFTGLOW</span>
    </div>

    <svg class="abs" style="left:60px;top:560px" width="260" height="230" aria-hidden="true">
      <circle cx="94" cy="138" r="75" fill="var(--lilac)" opacity=".35"/>
      <circle cx="172" cy="158" r="58" fill="var(--pink-soft)" opacity=".4"/>
    </svg>

    <div class="abs services">
      <h2>SERVICES:</h2>
      <h3>FACIALS</h3>
      <p>Sora Facial</p>
      <p>Vitamin C facial<br>Brightening treatment</p>
      <p>Tokari Signature Facial</p>
      <p>Tokari Ultimate Tranquility</p>
      <p>Tokari Man</p>
      <p>Clear Back Renewal</p>
      <h3>MASSAGE</h3>
      <p>Full body Hot Stone Massage</p>
      <p>Body massage</p>
      <p>Back massage</p>
      <h3>FOR YOUR FEET</h3>
      <p>Tiptoe calm massage</p>
      <p>Yume Feet<br>means gentle renewal</p>
      <h3>EYES</h3>
      <p>Lash tint • Brow tint</p>
      <h3>WAXING</h3>
    </div>

    <p class="abs call">Call to make an appointment:<span class="phone">(012) 555 0148</span></p>
  </section>

  <section class="panel panel--front">
    <svg class="abs" style="left:0;top:0" width="387" height="300" aria-hidden="true">
      <defs>
        <linearGradient id="photo-tone" x1="0" y1="0" x2="1" y2="1">
          <stop offset="0" stop-color="#d6e4f3"/>
          <stop offset=".5" stop-color="#efcfbf"/>
          <stop offset="1" stop-color="#e8c2b0"/>
        </linearGradient>
      </defs>
      <path d="M26 150 Q40 30 200 14 L387 10 L387 234 Q300 284 190 286 Q30 286 26 150 Z" fill="url(#photo-tone)"/>
      <path d="M8 185 Q28 14 387 6" fill="none" stroke="var(--blue)" stroke-width="8"/>
      <path d="M22 150 Q10 290 190 289 Q300 286 387 234" fill="none" stroke="var(--pink)" stroke-width="9" opacity=".85"/>
    </svg>
    <div class="abs" role="img" aria-label="Photo of a woman relaxing during a back massage" style="left:26px;top:12px;width:361px;height:272px"></div>
    <div class="abs" role="img" aria-label="Pink blossom illustration"
         style="left:250px;top:218px;width:128px;height:126px;border-radius:50%;background:radial-gradient(circle,#fdf0f5 0%,var(--pink-soft) 75%,rgba(242,182,207,0) 100%)"></div>

    <svg class="abs" style="left:0;top:380px" width="387" height="360" aria-hidden="true">
      <circle cx="188" cy="83" r="110" fill="#ffffff" opacity=".22"/>
      <circle cx="133" cy="248" r="88" fill="var(--lilac)" opacity=".4"/>
      <circle cx="248" cy="193" r="72" fill="var(--blue)" opacity=".3"/>
      <circle cx="293" cy="248" r="62" fill="var(--pink-soft)" opacity=".45"/>
    </svg>

    <div class="abs wordmark front-mark">
      <span class="name">Tokari</span>
      <span class="sub">SOFTGLOW</span>
    </div>

    <p class="abs address">Address information goes here<br>Telephone no. <span class="dot">•</span> Email or other info</p>
  </section>

</main>
</body>
</html>
```